Executive Business Card for Healthcare Company [Need Today]

I need a business card design for a healthcare company. The only branding the company has thus far is a logo. The cards will be utilized by company executives. The design I envision will be vibrant and appealing but with a corporate feel. They shouldn't be too casual or playful. I would like to complete this project TODAY if possible.

Target Market(s)

Healthcare vendors, other executives in healthcare and pharmaceuticals

Industry/Entity Type

Pharmaceutical

Contact Information for Business Card

See attachment

Font styles to use
Serif
Sans Serif

Colors

Designer to choose colors to be used in the design.

```html
<!DOCTYPE html>
<html lang="en">
<head>
<meta charset="utf-8">
<title>Corvane Therapeutics – Business Card</title>
<link href="https://fonts.googleapis.com/css2?family=Raleway:wght@300;400;600&display=swap" rel="stylesheet">
<style>
  :root {
    --bg: #e4e5e7;
    --card: #ffffff;
    --card-back: #f7f7f7;
    --teal: #1ea8b4;
    --green: #4db586;
    --ink: #4a4a4a;
    --ink-soft: #6b6b6b;
    --rule: #9a9a9a;
    --shade: #8d8d8d;
  }
  * { margin: 0; padding: 0; box-sizing: border-box; }
  html, body { width: 1200px; height: 726px; overflow: hidden; }
  body {
    background: var(--bg);
    font-family: "Raleway", Arial, sans-serif;
    color: var(--ink);
    position: relative;
  }
  .card {
    position: absolute;
    top: 214px;
    width: 520px;
    height: 297px;
    border-radius: 3px;
    box-shadow: 0 8px 22px rgba(0,0,0,0.16);
    overflow: hidden;
  }
  .card--front { left: 45px; background: var(--card); }
  .card--back { left: 635px; background: var(--card-back); }

  /* Front */
  .brand {
    position: absolute;
    left: 0; right: 0; top: 92px;
    display: flex; align-items: center; justify-content: center; gap: 16px;
  }
  .brand__circle {
    width: 62px; height: 62px;
    border: 3px solid var(--teal);
    border-radius: 50%;
  }
  .brand__rule { width: 1px; height: 58px; background: var(--rule); }
  .brand__name {
    font-weight: 400;
    font-size: 30px;
    line-height: 1.05;
    color: var(--teal);
  }
  .front__web {
    position: absolute;
    left: 0; right: 0; bottom: 56px;
    text-align: center;
    font-size: 14px;
    letter-spacing: 4px;
    color: var(--ink);
  }
  .front__web span { color: var(--teal); }

  /* Back */
  .back__panel { position: absolute; top: 0; left: 0; width: 520px; height: 297px; }
  .person { position: absolute; left: 34px; top: 40px; }
  .person__name { font-weight: 600; font-size: 22px; color: var(--teal); }
  .person__title { font-size: 11px; color: var(--ink); margin-top: 4px; padding-left: 10px; }
  .contact {
    position: absolute; left: 34px; bottom: 34px;
    list-style: none; font-size: 13px; color: var(--ink); line-height: 20px;
  }
  .contact li { display: flex; align-items: center; gap: 8px; }
  .contact svg { width: 12px; height: 12px; flex: none; }
  .contact .contact__plain { padding-left: 20px; }
  .panel-brand {
    position: absolute; right: 30px; top: 96px; width: 140px;
    display: flex; flex-direction: column; align-items: center; gap: 12px;
  }
  .panel-brand__circle { width: 46px; height: 46px; border: 2px solid #fff; border-radius: 50%; }
  .panel-brand__name {
    font-weight: 400; font-size: 17px; line-height: 1.15;
    color: #fff; text-align: center;
  }
</style>
</head>
<body>
  <section class="card card--front" aria-label="Card front">
    <div class="brand">
      <div class="brand__circle"></div>
      <div class="brand__rule"></div>
      <div class="brand__name">Corvane<br>Therapeutics</div>
    </div>
    <p class="front__web">www.<span>corvanerx</span>.com</p>
  </section>

  <section class="card card--back" aria-label="Card back">
    <svg class="back__panel" viewBox="0 0 520 297" aria-hidden="true">
      <defs>
        <linearGradient id="panelFill" x1="0" y1="1" x2="1" y2="0">
          <stop offset="0" stop-color="#1ea8b4"/>
          <stop offset="1" stop-color="#4db586"/>
        </linearGradient>
      </defs>
      <path d="M330 0 C 390 40, 400 110, 360 170 C 330 220, 322 262, 328 297 L 340 297 C 336 262, 344 222, 372 172 C 410 110, 400 40, 342 0 Z" fill="var(--shade)"/>
      <path d="M340 0 C 400 40, 410 110, 372 170 C 344 220, 336 262, 340 297 L 520 297 L 520 0 Z" fill="url(#panelFill)"/>
    </svg>

    <div class="person">
      <h1 class="person__name">Daniel Merrow</h1>
      <p class="person__title">Senior Director of Marketing</p>
    </div>

    <ul class="contact">
      <li><svg viewBox="0 0 12 12"><path d="M1 4 C1 2,3 1,6 1 C9 1,11 2,11 4 L9 5 L8 3.5 C7 3.2,5 3.2,4 3.5 L3 5 Z M3 6 H9 L10 11 H2 Z" fill="var(--teal)"/></svg>555-201-4830</li>
      <li><svg viewBox="0 0 12 12"><rect x="3" y="0.5" width="6" height="11" rx="1.2" fill="var(--teal)"/><rect x="4" y="2" width="4" height="7" fill="#fff"/></svg>555-201-7712</li>
      <li><svg viewBox="0 0 12 12"><circle cx="6" cy="6" r="5" fill="none" stroke="var(--teal)" stroke-width="1.4"/><path d="M1 6 H11 M6 1 C3 4,3 8,6 11 M6 1 C9 4,9 8,6 11" fill="none" stroke="var(--teal)" stroke-width="1"/></svg>dmerrow@corvanerx.com</li>
      <li class="contact__plain">118 N Linden Avenue</li>
      <li class="contact__plain">Marlow, GA 30999</li>
    </ul>

    <div class="panel-brand">
      <div class="panel-brand__circle"></div>
      <div class="panel-brand__name">Corvane<br>Therapeutics</div>
    </div>
  </section>
</body>
</html>
```